Vensol Holdings Web Design

Vensol Holdings Limited Shenzhen

This project is a 10 page launch website.
Our client is seeking a contemporary homepage design for a Holdings company. Once we are happy with the homepage design and select designer we will request a secondary page design.

Please see attached company LOGO for an idea of style, it incorporates the traditional Chinese furniture lattice work. The Corvel crest website is one of our clients favorite so we would like to see a similar homepage design to this website.

Use the websites below for reference purpose. The first two are Chinese and the second two are international. We would like to see elements of both but more focus on international design.

http://www.evergrande.com/http://www.taurenfield.com/pub/default.aspx http://www.corvelcrest.com/zh/maldives_lorinhaven/
http://www.quelba-studio.com
http://media-cache-ex0.snapvalu.com/originals/71/a3/19/71a319c5b2d04e8f6a17c3b9e5d0f4a1.jpg

Company Background
VENSOL HOLDINGS, located in Qianhai, China, is a new real-estate project operator, structuring urban-rural real-estate investment and development, and industrial fund investment. The company also invests in supply chain management and supporting infrastructures. To create new spaces and livable cities Vensol Holdings develop win-win strategic partnerships with a number of institutions. Currently cooperating with Tianjing North Lumore, China urban and rural integrated demonstration.

Target Market(s)

B2B property investment. Target market customers are senior level management/decision makers of large corporations. Focusing geographically on the domestic market first and expanding internationally in 2nd and 3rd years.

Industry/Entity Type

Investment

Requirements
Must have
• Since this is a new company, we would like to the website representing growth and power, E.g. like a growing tree.
Should not have
• Low-level vectors such as curency symbols, American dollar.

```html
<!DOCTYPE html>
<html lang="en">
<head>
<meta charset="utf-8">
<title>Vensol Holdings</title>
<link href="https://fonts.googleapis.com/css2?family=Open+Sans:wght@400;600;700&display=swap" rel="stylesheet">
<style>
  :root {
    --top-band: #838486;
    --header: #6d6e71;
    --gold: #c4a45a;
    --gold-light: #e3cc8c;
    --gold-dark: #a88a40;
    --cream: #f3ecd8;
    --white: #ffffff;
    --btn-top: #f0e7b8;
    --btn-mid: #e2c93a;
    --btn-bottom: #d8b82a;
  }
  * { margin: 0; padding: 0; box-sizing: border-box; }
  html, body { width: 1046px; height: 1200px; overflow: hidden; }
  body { font-family: "Open Sans", Arial, sans-serif; background: var(--header); position: relative; color: var(--white); }

  .top-band { position: absolute; left: 0; top: 0; width: 1046px; height: 80px; background: var(--top-band); border-bottom: 1px solid var(--gold); }

  .site-header { position: absolute; left: 0; top: 81px; width: 1046px; height: 155px; background: var(--header); }
  .brand { position: absolute; left: 56px; top: 20px; width: 134px; text-align: center; }
  .brand-circle { display: block; width: 74px; height: 74px; margin: 0 auto 6px; border: 2px solid var(--gold); border-radius: 50%; }
  .brand-name { font-size: 14px; font-weight: 400; color: var(--gold); letter-spacing: 0.3px; white-space: nowrap; }

  .search { position: absolute; left: 663px; top: 37px; display: flex; gap: 6px; }
  .search-field { width: 215px; height: 27px; background: var(--cream); border: 2px solid var(--gold); border-radius: 3px; }
  .search-button { width: 107px; height: 27px; border-radius: 3px; background: linear-gradient(var(--gold-light), var(--gold-dark)); display: flex; align-items: center; justify-content: center; gap: 6px; font-size: 12px; font-weight: 600; letter-spacing: 0.3px; color: var(--white); }

  .main-nav { position: absolute; right: 55px; top: 120px; display: flex; gap: 11px; font-size: 12.5px; text-transform: uppercase; letter-spacing: 0.1px; }

  .hero { position: absolute; left: 0; top: 236px; width: 1046px; height: 378px; background: linear-gradient(180deg, #b9cde4 0%, #d6e2ee 25%, #7fa058 50%, #4f7a3a 72%, #5d7250 100%); }
  .hero-title { position: absolute; left: 57px; top: 42px; font-size: 21px; color: var(--gold); font-weight: 400; }
  .hero-tagline { position: absolute; left: 57px; top: 74px; font-size: 12px; color: var(--gold); }

  .content { position: absolute; left: 0; top: 614px; width: 1046px; height: 548px; }
  .content-backdrop { position: absolute; inset: 0; background: linear-gradient(180deg, #6d6e72 0%, #6f7585 30%, #7a8db3 50%, #6d8dc2 62%, #5f6f5a 78%, #3f5a2e 100%); }

  .about { position: absolute; left: 56px; top: 16px; width: 570px; font-size: 12px; line-height: 19px; }
  .about p + p { margin-top: 18px; }
  .about strong { font-weight: 700; }

  .cta-row { position: absolute; left: 56px; top: 220px; display: flex; gap: 13px; }
  .cta { width: 178px; height: 85px; border: 2px solid var(--gold-light); border-radius: 4px; background: linear-gradient(180deg, var(--btn-top) 0%, #ede0a0 45%, var(--btn-mid) 46%, var(--btn-bottom) 100%); display: flex; align-items: center; justify-content: center; text-align: center; font-size: 17px; line-height: 24px; color: var(--white); text-transform: uppercase; }

  .divider { position: absolute; left: 678px; top: 32px; width: 1px; height: 290px; background: var(--gold); }

  .sidebar { position: absolute; left: 699px; top: 12px; width: 292px; font-size: 12px; line-height: 17.5px; }
  .sidebar h2 { font-size: 21px; font-weight: 400; color: var(--gold); line-height: 30px; }
  .sidebar address { font-style: normal; margin-top: 2px; }
  .sidebar .spacer { height: 17px; }
  .sidebar hr { border: 0; border-top: 1px solid var(--gold); margin: 12px 0 8px; }
  .sidebar .note { color: var(--gold); }
  .sidebar ul { list-style: none; margin-top: 17px; }

  .site-footer { position: absolute; left: 0; top: 1162px; width: 1046px; height: 38px; background: linear-gradient(90deg, var(--gold-dark) 0%, #f4ead0 50%, var(--gold-dark) 100%); display: flex; justify-content: center; align-items: center; gap: 8px; }
  .social-dot { width: 23px; height: 23px; border: 2px solid var(--gold-dark); border-radius: 50%; }
</style>
</head>
<body>
  <div class="top-band"></div>

  <header class="site-header">
    <div class="brand">
      <span class="brand-circle"></span>
      <span class="brand-name">Vensol Holdings</span>
    </div>
    <div class="search">
      <div class="search-field"></div>
      <div class="search-button">
        <svg width="16" height="16" viewBox="0 0 16 16" aria-hidden="true">
          <circle cx="8" cy="8" r="7" fill="none" stroke="#fff" stroke-width="1.3"/>
          <circle cx="7.2" cy="7.2" r="3" fill="none" stroke="#fff" stroke-width="1.3"/>
          <line x1="9.4" y1="9.4" x2="11.5" y2="11.5" stroke="#fff" stroke-width="1.5"/>
        </svg>
        SEARCH
      </div>
    </div>
    <nav class="main-nav">
      <span>Home</span>
      <span>About Vensol Holdings</span>
      <span>News Center</span>
      <span>Our Projects</span>
      <span>Group Business</span>
      <span>Corporate Culture</span>
      <span>Contact Us</span>
    </nav>
  </header>

  <section class="hero" role="img" aria-label="Photo of a Chinese garden with red-roofed pavilions, a scholar rock and willows beside a pond">
    <h1 class="hero-title">Vensol Holdings</h1>
    <p class="hero-tagline">Lorem ipsum dolor sit amet, consectetur adipiscing elit</p>
  </section>

  <main class="content">
    <div class="content-backdrop" role="img" aria-label="Photo of a hilltop pagoda palace among trees under a blue sky"></div>

    <div class="about">
      <p><strong>VENSOL HOLDINGS</strong> located in Qianhai, China, is a new real-estate project operator, structuring urban-rural real-estate investment and development, and industrial fund investment.</p>
      <p>The company also invests in supply chain management and supporting infrastructures.<br>To create new spaces and livable cities Vensol Holdings develop win-win strategic partnerships with a number of institutions. Currently cooperating with Tianjing North Lumore, China urban and rural integrated demonstration.</p>
    </div>

    <div class="cta-row">
      <div class="cta">Lorem ipsum<br>dolor</div>
      <div class="cta">Lorem ipsum<br>dolor</div>
      <div class="cta">Lorem ipsum<br>dolor</div>
    </div>

    <div class="divider"></div>

    <aside class="sidebar">
      <h2>Contact Information</h2>
      <address>
        Suite 123, Address Road Boulevard<br>Qianhai, China
        <div class="spacer"></div>
        Tel +0755 284 9031<br>Fax +0755 284 9031<br>E-mail info@vensolholdings.com
      </address>
      <hr>
      <h2>Lorem ipsum dolor sit amet,</h2>
      <p class="note">consectetur adipiscing elit.<br>Nam non malesuada enim. Suspendisse potenti.</p>
      <ul>
        <li>About Vensol Holdings</li>
        <li>Architecture</li>
        <li>Corporate Social Responsibility</li>
        <li>Meet the General Manager</li>
      </ul>
    </aside>
  </main>

  <footer class="site-footer">
    <span class="social-dot"></span>
    <span class="social-dot"></span>
    <span class="social-dot"></span>
    <span class="social-dot"></span>
  </footer>
</body>
</html>
```